STAINLESS UNTESIL HOLDER AND UNTESIL SET DESIGN

I want two package design, one is for stainless utensil holder. another is for whole set of utensil with the stainless utensil holder.
The first product is just going to be the holder itself. The dimensions on this are. 4.3 x 4.3 x 7 in inches. That is what we would like the box to be

The second product is going to be the holder, but with the kitchen utensils as well. The dimensions are. 4.3 x 4.3 x 14.3 for the box as well.

For both products we would like a nice modern and sleek design showcasing our products. We would like our images to use, and not copies of similar products found online, this is important to us as there are slight differences with most found on the market. We will be attaching the pictures on a separate message.

Product 1 (holder alone) - We would like our logo (QX7) and product called Stainless Steel Holder. We would like to showcase some attributes written on the box, like a removable bottom easy for cleaning, lightweight, stainless steel.

Product 2- We would like our logo, and product to be called Kitchen Utensil Set with Holder. We would like a somewhat similar design to product 1 but with key features including the holder and also listed what is to be included in that set. Tongs, Ladle, turning spatula, spatula, spaghetti spoon, slotted spoon, holder.

we need to show: stainless utensil holder.
with a removable bottom
easy for cleaning, lightweight, stainless steel. (you can add some for us too if you have any idea better than us)
second product ,
we need to list 7 pcs kitchen utensil sets,
Tongs, Ladle, turning spatula, spatula, spaghetti spoon, slotted spoon, stainless holder.
silicone head, beech wood handle, NRQ material ,(pls put on one NRQ logo),BPA free, heat resistant up to 480 f, leaking removable bottom design for stainless holder, easy for cleaning, (if you have any suggestion, you can add for us)

Target Market(s)

Tarvolo KLP, middle to higher class families, females 18-60

Font styles to use
Other font styles liked:
• designer's choice

Requirements
Must have
• 2 designs one for just the holder the other for the utensils and holder
• sleek design
• Modern design
• Barcode
• Correct Dimensions
• PDF Source FIle
• Ready to print
• Our picture of our product,
Nice to have
• A great and very unique design that stands out
Should not have
• Other peoples product design copy and pasted
• Other peoples utensil set
• cheap crude design

```html
<!DOCTYPE html>
<html lang="en">
<head>
<meta charset="utf-8">
<title>QX7 Kitchen Utensil Set with Holder – Packaging Panels</title>
<link href="https://fonts.googleapis.com/css2?family=Lato:wght@300;400&display=swap" rel="stylesheet">
<style>
  :root {
    --page-bg: #e6e6e6;
    --panel-white: #ffffff;
    --brand-green: #6aac4c;
    --brand-green-dark: #5c9a40;
    --brand-blue: #3fb4dd;
    --brand-blue-dark: #2fa2cc;
    --ink: #4a4a4a;
    --ink-soft: #7a7a7a;
    --steel-light: #d9d9d6;
    --steel-dark: #6e675e;
    --silicone: #2f3336;
  }
  * { margin: 0; padding: 0; box-sizing: border-box; }
  html, body {
    width: 1200px; height: 913px; overflow: hidden;
    background: var(--page-bg);
    font-family: "Lato", sans-serif;
  }
  .dieline {
    position: absolute; left: 342px; top: 26px;
    display: flex; width: 516px; height: 860px;
    box-shadow: 0 10px 30px rgba(0,0,0,.18);
  }
  .panel {
    position: relative; width: 258px; height: 860px;
    overflow: hidden; background: var(--panel-white);
  }
  .panel-bg { position: absolute; inset: 0; }

  /* brand mark */
  .brand {
    position: absolute; display: flex; align-items: center; gap: 6px;
    font-weight: 400; font-size: 15px; letter-spacing: .5px;
  }
  .brand-dot { width: 16px; height: 16px; border-radius: 50%; }
  .side-panel .brand { left: 24px; top: 30px; color: var(--ink-soft); }
  .side-panel .brand-dot { background: var(--brand-blue); }
  .front-panel .brand { right: 22px; top: 34px; color: #fff; }
  .front-panel .brand-dot { background: #fff; }

  .product-title {
    position: absolute; left: 24px;
    font-weight: 300; font-size: 46px; line-height: .92;
    letter-spacing: -.5px;
  }
  .side-panel .product-title { top: 120px; color: var(--ink); }
  .front-panel .product-title { top: 96px; color: #fff; }

  /* side panel copy */
  .feature-copy {
    position: absolute; left: 26px; top: 440px; width: 210px;
    color: #fff; font-size: 13px; line-height: 1.35; list-style: none;
  }
  .feature-copy li::before { content: "• "; }
  .set-heading {
    position: absolute; left: 26px; top: 528px;
    color: #fff; font-size: 13px;
  }
  .set-list { top: 548px; }

  .cert-row {
    position: absolute; display: flex; gap: 8px; align-items: center;
  }
  .side-panel .cert-row { right: 18px; bottom: 22px; flex-direction: column; }
  .cert-badge { width: 26px; height: 26px; border-radius: 50%; background: rgba(255,255,255,.85); }
  .cert-badge.square { border-radius: 4px; }
  .front-panel .cert-row { left: 24px; bottom: 22px; }
  .front-panel .cert-badge { background: #9a9a9a; width: 24px; height: 24px; }
  .front-panel .cert-badge.large { width: 34px; height: 34px; }

  .product-shot {
    position: absolute; left: 64px; top: 420px; width: 116px; height: 340px;
    border-radius: 44px 44px 10px 10px;
    background: linear-gradient(180deg, var(--silicone) 0%, var(--silicone) 48%, var(--steel-light) 60%, var(--steel-dark) 100%);
  }
  .callout-lines { position: absolute; inset: 0; pointer-events: none; z-index: 1; }
  .callout {
    position: absolute; z-index: 2;
    font-size: 10px; line-height: 1.15; color: var(--ink); white-space: nowrap;
  }
  .callout-lightweight { left: 192px; top: 596px; }
  .callout-steel { left: 14px; top: 688px; }
  .callout-bottom { left: 30px; top: 770px; }
  .approval-badge {
    position: absolute; right: 24px; bottom: 30px;
    width: 40px; height: 24px; border-radius: 3px; background: var(--ink);
  }
</style>
</head>
<body>
  <main class="dieline">
    <!-- side panel -->
    <section class="panel side-panel">
      <svg class="panel-bg" viewBox="0 0 258 860" preserveAspectRatio="none" aria-hidden="true">
        <path d="M0 400 C 80 360, 170 370, 258 420 L258 860 L0 860 Z" fill="var(--brand-blue)"/>
      </svg>
      <div class="brand"><span class="brand-dot"></span>QX7</div>
      <h1 class="product-title">kitchen<br>utensil<br>set with<br>holder</h1>
      <ul class="feature-copy">
        <li>easy for cleaning</li>
        <li>removable bottom</li>
        <li>lightweight</li>
        <li>stainless steel</li>
      </ul>
      <p class="set-heading">This set contains:</p>
      <ul class="feature-copy set-list">
        <li>Tongs</li>
        <li>Ladle</li>
        <li>turning spatula</li>
        <li>spatula</li>
        <li>spaghetti spoon</li>
        <li>slotted spoon</li>
        <li>holder</li>
      </ul>
      <div class="cert-row">
        <span class="cert-badge square"></span>
        <span class="cert-badge"></span>
        <span class="cert-badge"></span>
      </div>
    </section>

    <!-- front panel -->
    <section class="panel front-panel">
      <svg class="panel-bg" viewBox="0 0 258 860" preserveAspectRatio="none" aria-hidden="true">
        <path d="M0 0 L258 0 L258 420 C 180 470, 80 500, 0 480 Z" fill="var(--brand-green)"/>
      </svg>
      <div class="brand"><span class="brand-dot"></span>QX7</div>
      <h1 class="product-title">kitchen<br>utensil<br>set with<br>holder</h1>
      <div class="product-shot" role="img" aria-label="Product photo: black silicone utensils with beech wood handles standing in a perforated stainless steel holder"></div>
      <svg class="callout-lines" viewBox="0 0 258 860" aria-hidden="true">
        <polyline points="248,610 190,610 166,650" fill="none" stroke="var(--ink)" stroke-width=".8"/>
        <polyline points="14,714 56,714 76,694" fill="none" stroke="var(--ink)" stroke-width=".8"/>
        <polyline points="30,798 104,798 118,752" fill="none" stroke="var(--ink)" stroke-width=".8"/>
      </svg>
      <span class="callout callout-lightweight">lightweight</span>
      <span class="callout callout-steel">stainless<br>steel</span>
      <span class="callout callout-bottom">easy for cleaning<br>removable bottom</span>
      <div class="approval-badge"></div>
      <div class="cert-row">
        <span class="cert-badge"></span>
        <span class="cert-badge large"></span>
      </div>
    </section>
  </main>
</body>
</html>
```